BrivoTerna. Lantern of the Steady Harvest. Business card

Professional business card for BrivoTerna (Lantern of the Steady Harvest)
My rationale: Strategy-> Execution-> Results-> Value that lead to the BrivoTerna name: We put the Lantern of the Steady Harvest.
We deliver value to our customers helping them at defining a good strategy (cyan arrow). 90% of well formulated strategies fail due to poor execution so we also consider strategical execution very important (green arrow). Due to the execution we obtain the results (blue arrow). Finally, the results provide feedback to redefine strategy, and the new strategy has to be executed and new results obtained providing new feedback and on and on. It's like a wheel that finally, must create corporate value: value for shareholders, staholders, employees, providers...-

Target Market(s)

CEOs and steering comitees , invewrnent funds

Industry/Entity Type

Business Consultant

Contact Information for Business Card

Teodoro Vinsquel
CEO & Founder
teodoro.vinsquel@brivoterna-example.com
Mobile: +34 655.803.912
www.brivoterna-example.com

Colors

Designer to choose colors to be used in the design.

Requirements
Nice to have
• Nice to hace the words: Strategy, execution, results
• Nice to vave the claim: Lantern of the Steady Harvest
• The three colors should be shown:
• cyan for STRATEGY
• green for EXECUTION
• blue for RESULTS
Should not have
• Complete black background

```html
<!DOCTYPE html>
<html lang="en">
<head>
<meta charset="utf-8">
<title>BrivoTerna – Business Card</title>
<link href="https://fonts.googleapis.com/css2?family=Open+Sans:wght@400;600;700;800&display=swap" rel="stylesheet">
<style>
  :root {
    --backdrop: #2c2c2e;
    --brand-blue: #243f8c;
    --brand-green: #9acb3c;
    --brand-cyan: #29abe2;
    --paper: #ffffff;
    --ink: #2a2f45;
  }
  * { box-sizing: border-box; margin: 0; padding: 0; }
  html, body {
    width: 1200px; height: 900px; overflow: hidden;
    background: var(--backdrop);
    font-family: "Open Sans", Arial, sans-serif;
  }
  .stage {
    width: 1200px; height: 900px;
    display: flex; flex-direction: column; align-items: center; justify-content: center;
    gap: 30px;
  }
  .card {
    position: relative;
    width: 700px; height: 400px;
    overflow: hidden;
    box-shadow: 0 12px 30px rgba(0,0,0,.45);
  }

  /* Front */
  .card-front { background: var(--brand-blue); color: var(--paper); }
  .front-brand {
    position: absolute; left: 0; right: 0; top: 130px;
    text-align: center;
    font-weight: 800; font-size: 70px; letter-spacing: -1px;
    color: var(--paper);
  }
  .front-rule {
    position: absolute; left: 36px; right: 36px; top: 300px;
    height: 2px; background: var(--brand-green);
  }
  .pillars {
    position: absolute; left: 36px; right: 36px; top: 318px;
    display: flex; justify-content: space-between;
    font-weight: 800; font-size: 19px; letter-spacing: .5px; text-transform: uppercase;
  }
  .pillar-strategy { color: var(--paper); }
  .pillar-execution { color: var(--brand-green); }
  .pillar-results { color: var(--brand-cyan); }

  /* Back */
  .card-back { background: var(--paper); color: var(--ink); }
  .back-brand {
    position: absolute; left: 38px; top: 26px;
    font-weight: 800; font-size: 64px; letter-spacing: -1px;
    color: var(--brand-blue);
  }
  .holder { position: absolute; left: 42px; top: 128px; }
  .holder-name {
    font-weight: 800; font-size: 27px; text-transform: uppercase; letter-spacing: .5px;
    color: var(--brand-blue); line-height: 1.1;
  }
  .holder-role { font-size: 18px; color: var(--brand-green); line-height: 1.1; }
  .contacts {
    position: absolute; left: 42px; top: 200px;
    list-style: none; font-size: 18px; line-height: 27px; color: var(--ink);
  }
  .contacts li { display: flex; align-items: center; gap: 10px; }
  .contacts svg { width: 18px; height: 18px; flex: none; }
  .back-rule {
    position: absolute; left: 42px; top: 296px;
    width: 380px; height: 2px; background: var(--brand-green);
  }
  .tagline {
    position: absolute; left: 42px; top: 312px;
    font-size: 20px; text-transform: uppercase; letter-spacing: .3px; color: var(--ink);
  }
  .back-bands { position: absolute; left: 0; bottom: 0; width: 700px; height: 40px; }
</style>
</head>
<body>
<main class="stage">

  <section class="card card-front" aria-label="Card front">
    <div class="front-brand">BrivoTerna</div>
    <div class="front-rule"></div>
    <div class="pillars">
      <span class="pillar-strategy">Strategy</span>
      <span class="pillar-execution">Execution</span>
      <span class="pillar-results">Results</span>
    </div>
  </section>

  <section class="card card-back" aria-label="Card back">
    <div class="back-brand">BrivoTerna</div>
    <div class="holder">
      <div class="holder-name">Teodoro Vinsquel</div>
      <div class="holder-role">CEO &amp; Founder</div>
    </div>
    <ul class="contacts">
      <li>
        <svg viewBox="0 0 24 24" aria-hidden="true"><path d="M6.6 3.5l3 3-1.8 2.3a12 12 0 0 0 7.4 7.4l2.3-1.8 3 3-2.2 2.6C11 19.5 4.5 13 3.9 5.7z" fill="none" stroke="var(--brand-cyan)" stroke-width="1.8" stroke-linejoin="round"/></svg>
        +34 655.803.912
      </li>
      <li>
        <svg viewBox="0 0 24 24" aria-hidden="true"><rect x="2.5" y="5" width="19" height="14" fill="none" stroke="var(--brand-cyan)" stroke-width="1.8"/><path d="M2.5 5l9.5 8 9.5-8" fill="none" stroke="var(--brand-cyan)" stroke-width="1.8"/></svg>
        teodoro.vinsquel@brivoterna-example.com
      </li>
      <li>
        <svg viewBox="0 0 24 24" aria-hidden="true"><circle cx="12" cy="12" r="9.5" fill="var(--brand-cyan)"/><path d="M2.5 12h19M12 2.5c-3.5 3.5-3.5 15.5 0 19M12 2.5c3.5 3.5 3.5 15.5 0 19M4.5 7h15M4.5 17h15" fill="none" stroke="#fff" stroke-width="1.3"/></svg>
        www.brivoterna-example.com
      </li>
    </ul>
    <div class="back-rule"></div>
    <div class="tagline">Lantern of the Steady Harvest</div>
    <svg class="back-bands" viewBox="0 0 700 40" aria-hidden="true">
      <rect class="band-green" x="0" y="28" width="360" height="12" fill="var(--brand-green)"/>
      <polygon class="band-blue" points="390,40 412,16 700,16 700,40" fill="var(--brand-blue)"/>
    </svg>
  </section>

</main>
</body>
</html>
```